Steel Rebar Fabrication Company needs Facebook Ads & page, Instagram Ads & pages designed.

I want to put out an Instagram, Facebook ad, and LinkedIn campaign out for my new company, Ridgeline Metals Inc. I want the ads to be short but clean, clear and precise. I want our address: 4871 Marrowfield Rd. Tsawwassen, BC. I want our hours of operation to be listed 8:00am to 4:00pm Monday to Friday. Product Delivery to your job site or pick up at our yard available. We can cut, bend to custom and standard shapes based upon Canadian CSA Standards. We offer products ranging from 10mm to 35mm diameter Grade 400W rebar. We can bend stirrups, dowels, hairpins; whatever your company needs to complete your product. Whether it is a small project, Tilt Up warehouse, Wood Frame Construction with Concrete parkade foundation; we have the team to meet your needs.
Email address: info@ridgelinemetalsinc.ca
We can service all areas of British Columbia.

Target Market(s)

Construction Company's for homes, condominiums, warehouses, commercial, industrial, and infrastructure projects. As well, as the every day DIY home improvement or renovator.

Industry/Entity Type

Construction

Requirements
Nice to have
• Would like to see a image of the rebar steel that I have provided in the ad. Even if it is in the background with a lower opacity level. Bonus if someone includes any of the movie files I have uploaded.

```html
<!DOCTYPE html>
<html lang="en">
<head>
<meta charset="utf-8">
<title>Ridgeline Metals Inc. — Need Steelwork?</title>
<link rel="stylesheet" href="https://fonts.googleapis.com/css2?family=Montserrat:wght@400;500;700;800&display=swap">
<style>
  :root {
    --paper: #ffffff;
    --ink: #1b1b1b;
    --circle-light: #d6d6d6;
    --circle-warm: #bfbbbb;
    --wire-tone: #c9ccd0;
    --wire-edge: #8a8d92;
  }
  * { margin: 0; padding: 0; box-sizing: border-box; }
  html, body { width: 1200px; height: 1200px; overflow: hidden; background: var(--paper); }
  .ad {
    position: relative;
    width: 1200px;
    height: 1200px;
    overflow: hidden;
    background: var(--paper);
    font-family: "Montserrat", Arial, sans-serif;
    color: var(--ink);
  }
  .circle { position: absolute; border-radius: 50%; }
  .circle--left { width: 600px; height: 600px; left: -228px; top: 211px; background: var(--circle-light); }
  .circle--bottom { width: 588px; height: 588px; left: 578px; top: 884px; background: var(--circle-warm); }

  .rebar-visual {
    position: absolute;
    left: 540px;
    top: 0;
    width: 660px;
    height: 400px;
    background: radial-gradient(ellipse at 55% 40%, var(--wire-tone) 0%, rgba(201,204,208,0.45) 40%, rgba(255,255,255,0) 72%);
  }

  .brand {
    position: absolute;
    left: 58px;
    top: 70px;
    font-weight: 800;
    font-size: 44px;
    line-height: 1.05;
    letter-spacing: 1px;
    color: var(--ink);
  }

  .headline {
    position: absolute;
    left: 54px;
    top: 282px;
    font-weight: 800;
    font-size: 124px;
    line-height: 128px;
    letter-spacing: 1px;
    text-transform: uppercase;
  }

  .subhead {
    position: absolute;
    left: 58px;
    top: 550px;
    font-weight: 700;
    font-size: 34px;
    line-height: 40px;
  }

  .features {
    position: absolute;
    left: 58px;
    top: 726px;
    list-style: none;
    font-weight: 400;
    font-size: 30px;
    line-height: 53px;
  }

  .contact {
    position: absolute;
    right: 58px;
    top: 968px;
    text-align: right;
    font-weight: 400;
    font-size: 31px;
    line-height: 50px;
  }
  .contact__email { margin-top: 40px; }
</style>
</head>
<body>
  <main class="ad">
    <div class="circle circle--left"></div>
    <div class="circle circle--bottom"></div>
    <div class="rebar-visual" role="img" aria-label="Photo of a bent steel rebar wire coiled into a spring shape"></div>

    <div class="brand">RIDGELINE<br>METALS INC.</div>

    <h1 class="headline">Need<br>Steelwork?</h1>

    <p class="subhead">We will help you cut / bend to custom / standard shapes<br>based upon Canadian CSA Standards</p>

    <ul class="features">
      <li>&gt; Products ranging from 10mm to 35mm diameter Grade 400W rebar</li>
      <li>&gt; Product Delivery to your job site / pick up at our yard available</li>
      <li>&gt; Service all areas of British Columbia</li>
    </ul>

    <address class="contact" style="font-style: normal;">
      <p>4871 Marrowfield Rd. Tsawwassen, BC.</p>
      <p>Available 8:00am - 4:00pm Mon- Fri</p>
      <p class="contact__email">info@ridgelinemetalsinc.ca</p>
    </address>
  </main>
</body>
</html>
```